Tax Preparation flyer for LedgerVale Corp.

My Client would like a one page PDF flyer to promote upcoming tax season in Canada. This firm is affordable and all virtual. I have attached a copy of their logo and a word document with the proposed wording for the flyer. Please feel free to change if you have better suggestions.

Target Market(s)

individuals in canada

Colors
0054AA
0677BA
7BADD7
CADEEF
E8F1F8

```html
<!DOCTYPE html>
<html lang="en">
<head>
<meta charset="utf-8">
<title>LedgerVale Corp. – Tax Season Flyer</title>
<link rel="stylesheet" href="https://fonts.googleapis.com/css2?family=Poppins:wght@300;400;500;600;700;800&display=swap">
<style>
  :root {
    --stage: #9fb0aa;
    --brand-deep: #0054AA;
    --brand-blue: #0677BA;
    --brand-sky: #7BADD7;
    --brand-mist: #CADEEF;
    --brand-ice: #E8F1F8;
    --panel-blue: rgba(6, 119, 186, 0.9);
    --side-teal: rgba(8, 52, 74, 0.85);
    --pill: rgba(222, 226, 228, 0.55);
    --white: #ffffff;
    --photo-dark: #2a1d17;
    --photo-warm: #6b5242;
    --photo-tan: #a88b6f;
  }
  * { margin: 0; padding: 0; box-sizing: border-box; }
  html, body { width: 1200px; height: 800px; overflow: hidden; }
  body {
    background: var(--stage);
    font-family: "Poppins", sans-serif;
    color: var(--white);
    position: relative;
  }
  .flyer {
    position: absolute;
    left: 333px; top: 20px;
    width: 534px; height: 760px;
    overflow: hidden;
    box-shadow: 0 4px 14px rgba(0,0,0,0.25);
  }
  .flyer-photo {
    position: absolute; inset: 0;
    background:
      radial-gradient(ellipse 45% 35% at 82% 55%, var(--photo-tan) 0%, rgba(168,139,111,0) 70%),
      radial-gradient(ellipse 30% 18% at 75% 22%, #c49a6c 0%, rgba(196,154,108,0) 70%),
      radial-gradient(ellipse 60% 20% at 40% 5%, rgba(40,90,120,0.7) 0%, rgba(40,90,120,0) 70%),
      linear-gradient(180deg, #4a3a30 0%, var(--photo-warm) 35%, var(--photo-dark) 100%);
  }
  .tagline {
    position: absolute; left: 13px; top: 65px;
    font-size: 8.4px; font-weight: 400; letter-spacing: 0.6px;
    text-transform: uppercase;
  }
  .headline-pill {
    position: absolute; left: 0; top: 83px;
    width: 269px; height: 98px;
    background: var(--pill);
    border-radius: 0 49px 49px 0;
  }
  .headline {
    position: absolute; left: 13px; top: 101px;
    font-size: 22.5px; font-weight: 700; line-height: 29px;
    color: var(--brand-ice);
  }
  .side-strip {
    position: absolute; left: 0; top: 190px; width: 51px; bottom: 0;
    background: var(--side-teal);
  }
  .side-lines { position: absolute; left: 0; top: 190px; }
  .info-panel {
    position: absolute; left: 62px; top: 190px;
    width: 287px; bottom: 0;
    background: var(--panel-blue);
    border-radius: 0 96px 0 0;
  }
  .quote-mark {
    position: absolute; left: 92px; top: 198px;
    font-size: 60px; font-weight: 800; line-height: 1;
    height: 40px; overflow: hidden;
  }
  .panel-title {
    position: absolute; left: 91px; top: 252px;
    font-size: 20.5px; font-weight: 700; line-height: 27px;
    color: var(--brand-ice);
  }
  .panel-title .underlined {
    border-bottom: 1.5px solid var(--white);
    padding-bottom: 1px;
  }
  .body-copy {
    position: absolute; left: 91px; top: 322px; width: 226px;
    font-size: 8.1px; font-weight: 300; line-height: 14.5px;
    text-align: justify;
    color: var(--brand-ice);
  }
  .body-copy p + p { margin-top: 10px; }
  .body-copy strong { font-weight: 600; color: var(--white); }
  .price-row {
    position: absolute; left: 91px; width: 226px; height: 34px;
    border: 1px solid var(--brand-sky);
    background: rgba(123, 173, 215, 0.15);
    display: flex; align-items: center; justify-content: space-between;
    padding: 0 6px 0 10px;
    font-weight: 600;
  }
  .price-row .service { font-size: 8.5px; }
  .price-row .amount { font-size: 10.5px; }
  .price-row--personal { top: 529px; }
  .price-row--business { top: 571px; }
  .note {
    position: absolute; left: 91px; width: 228px;
    display: flex; gap: 7px; align-items: center;
  }
  .note-icon {
    flex: 0 0 23px; height: 23px;
    background: var(--side-teal);
    border-radius: 3px;
    display: flex; align-items: center; justify-content: center;
  }
  .note-text {
    font-size: 6.5px; line-height: 11.8px; font-weight: 300;
    color: var(--brand-ice);
  }
  .note-text strong { font-weight: 600; color: var(--white); }
  .note--complex { top: 624px; }
  .note--behind { top: 665px; }
  .note--refund { top: 707px; }
  .brand-block {
    position: absolute; left: 368px; top: 663px; width: 158px;
    text-align: center;
  }
  .brand-name {
    font-size: 22px; font-weight: 600; line-height: 1.1;
    color: var(--white);
  }
  .contact {
    margin-top: 16px;
    font-size: 10px; line-height: 14px; font-weight: 400;
  }
</style>
</head>
<body>
  <main class="flyer">
    <div class="flyer-photo" role="img" aria-label="Photo of a smiling woman in a beige blazer talking on a phone in a cafe, with a colourful mural behind her"></div>

    <p class="tagline">Today so you can start to breathe easy.</p>
    <div class="headline-pill"></div>
    <h1 class="headline">Affordable &amp; All in<br>Virtual Services</h1>

    <div class="side-strip"></div>
    <svg class="side-lines" width="60" height="570" viewBox="0 0 60 570" aria-hidden="true">
      <path d="M0 30 L50 0 L50 570" fill="none" stroke="var(--brand-mist)" stroke-width="0.8"/>
      <path d="M0 30 Q32 40 32 70 L32 570" fill="none" stroke="var(--brand-mist)" stroke-width="0.8"/>
    </svg>

    <section class="info-panel"></section>
    <div class="quote-mark">”</div>
    <h2 class="panel-title">Relax, We’ve Got<br>Your <span class="underlined">Taxes Covered!</span></h2>

    <div class="body-copy">
      <p>Our tax preparers have over 20 years experience and worked both in public accounting firms as well as specialized tax. <strong>Our tax services are virtual</strong>, so you don’t have to take the time for a personal visit. We take care of everything and can access all your tax slips from the revenue agency directly into our tax software. All signing is done via secure e-signature.</p>
      <p>You can fill and submit the appropriate forms, along with all your other documents, in our secure client portal. It’s important that we understand your situation and any changes in your situation from the past year.</p>
    </div>

    <div class="price-row price-row--personal"><span class="service">Personal Tax Return</span><span class="amount">$100.00</span></div>
    <div class="price-row price-row--business"><span class="service">+ Business or Rental schedule</span><span class="amount">$125.00</span></div>

    <div class="note note--complex">
      <span class="note-icon"><svg width="13" height="12" viewBox="0 0 13 12" aria-hidden="true"><path d="M1 1h11v7H5l-3 3V8H1z" fill="none" stroke="var(--brand-mist)" stroke-width="1.2"/><path d="M3.5 3.5h6M3.5 5.5h4" stroke="var(--brand-mist)" stroke-width="1"/></svg></span>
      <p class="note-text">More complex tax returns will be assessed based on the complexity of the return and <strong>you will be advised before we start.</strong></p>
    </div>
    <div class="note note--behind">
      <span class="note-icon"><svg width="12" height="12" viewBox="0 0 12 12" aria-hidden="true"><path d="M9.5 4A4 4 0 1 0 10 7" fill="none" stroke="var(--brand-mist)" stroke-width="1.3"/><path d="M10 1v3.5H6.5" fill="none" stroke="var(--brand-mist)" stroke-width="1.3"/></svg></span>
      <p class="note-text">Did you fall behind in filing your income tax save 20% when you file 3 or more years with us. <strong>We can do back to 2012 for filing of tax returns.</strong></p>
    </div>
    <div class="note note--refund">
      <span class="note-icon"><svg width="13" height="11" viewBox="0 0 13 11" aria-hidden="true"><rect x="1" y="2.5" width="11" height="7.5" rx="1" fill="none" stroke="var(--brand-mist)" stroke-width="1.2"/><path d="M4.5 2.5V1h4v1.5" fill="none" stroke="var(--brand-mist)" stroke-width="1.1"/><circle cx="6.5" cy="6.2" r="1.7" fill="none" stroke="var(--brand-mist)" stroke-width="1"/></svg></span>
      <p class="note-text">If you expect a refund, <strong>the earlier you file the sooner you will receive your refund.</strong> Our average turn around time prior to April is a couple of days.</p>
    </div>

    <div class="brand-block">
      <p class="brand-name">LedgerVale</p>
      <p class="contact">Contact us:<br>hello@ledgervale.ca</p>
    </div>
  </main>
</body>
</html>
```